13 Varno - new website design project

Our company Varno Electrical is developing a new lead generation website focused on Electrical, LED Lighting and Solar Power. We need a high converting website.

Example of our current website is www.varnoelectrical-example.com.au You can take content from this website for this new design. Our colours are red, black and white. For our new website we would like to promote Varno, Spark Every Day. Please listen to the jingle.

The below link is the company jingle that we have developed.
http://www.tunecraftdemo.com.au/vrn-tc-v1/

The key for this brief is to generate leads for Electrical, LED Lighting (for commercial) and Solar Power & Storage.

Target Market(s)

Business owners in Melbourne Victoria

Number of Pages Required

4 page

Colors
ec1f27
ffffff

Requirements
Must have
• This page must be clean, be in line with company branding and a high converting lead website.

```html
<!DOCTYPE html>
<html lang="en">
<head>
<meta charset="utf-8">
<title>Varno Electrical — Spark Every Day</title>
<link href="https://fonts.googleapis.com/css2?family=Roboto:wght@400;500;700&family=Fira+Sans+Condensed:wght@500&display=swap" rel="stylesheet">
<style>
:root{
  --red:#ec1f27;
  --dark:#2b2d36;
  --darker:#24262e;
  --ink:#222;
  --body:#555;
  --light:#f0f0f0;
  --white:#fff;
  --rule:#ddd;
}
*{box-sizing:border-box;margin:0;padding:0}
html,body{width:1200px;height:3711px;overflow:hidden;background:var(--white)}
body{font-family:"Roboto",Arial,sans-serif;color:var(--body);position:relative}
.abs{position:absolute}
/* header */
.site-header{position:absolute;left:0;top:0;width:1200px;height:136px;background:var(--white)}
.brand{position:absolute;left:60px;top:14px;display:flex;align-items:center;gap:12px}
.brand-dot{width:52px;height:52px;border-radius:50%;background:var(--red)}
.brand-name{font-size:48px;font-weight:700;color:var(--dark);letter-spacing:1px}
.brand-tag{position:absolute;left:72px;top:80px;font-size:15px;color:var(--dark);font-weight:500}
.topbar{position:absolute;right:78px;top:22px;display:flex;align-items:center;gap:14px;font-size:15px;color:var(--ink)}
.topbar .ico{width:30px;height:30px;border-radius:50%;border:2px solid var(--red);display:flex;align-items:center;justify-content:center}
.social{display:flex;gap:8px}
.social span{width:30px;height:30px;border-radius:50%;background:var(--red);display:block}
.main-nav{position:absolute;left:346px;top:84px;width:854px;height:42px;background:var(--dark);display:flex;align-items:center;padding-left:24px;gap:0}
.main-nav a{color:var(--white);text-decoration:none;font-size:16px;font-weight:500;padding:0 38px;border-right:1px solid #444;line-height:42px}
.main-nav a.active{background:var(--red);border-radius:14px;line-height:32px;padding:0 28px;margin-right:30px;border:none}
/* hero */
.hero{position:absolute;left:0;top:136px;width:1200px;height:581px;background:linear-gradient(120deg,#6f7f93 0%,#a7b3c1 35%,#7b6d5b 70%,#3d3d44 100%)}
.hero-arrow{position:absolute;top:246px;width:40px;height:40px;background:rgba(0,0,0,.7);display:flex;align-items:center;justify-content:center}
.hero-caption{position:absolute;left:0;right:0;bottom:0;height:86px;background:rgba(0,0,0,.4);text-align:center;line-height:86px;font-family:"Fira Sans Condensed",Arial,sans-serif;font-size:38px;font-weight:500;color:var(--white)}
/* headings */
.sec-title{position:absolute;left:0;width:1200px;text-align:center;font-size:32px;font-weight:700;color:var(--ink);text-transform:uppercase}
.sec-title em{font-style:normal;color:var(--red)}
.sec-title::after{content:"";display:block;width:60px;height:3px;background:var(--red);margin:18px auto 0}
/* services */
.service-card{position:absolute;top:858px;width:328px;height:276px}
.service-card h3{height:68px;background:var(--dark);border-radius:10px 10px 0 0;color:var(--white);text-align:center;line-height:68px;font-size:21px;font-weight:500}
.service-card .photo{height:186px}
.btn{display:inline-flex;align-items:center;gap:10px;background:var(--red);color:var(--white);border-radius:20px;font-size:14px;font-weight:500;height:32px;padding:0 6px 0 22px;text-transform:uppercase}
.btn i{width:22px;height:22px;border-radius:50%;background:var(--dark);display:flex;align-items:center;justify-content:center}
.service-card .btn{position:absolute;left:50%;transform:translateX(-50%);bottom:6px}
/* about */
.about{position:absolute;left:0;top:1200px;width:1200px;height:453px;background:var(--light)}
.about .photo{position:absolute;left:0;top:0;width:599px;height:453px;background:linear-gradient(180deg,#d7dade,#9aa0a6 60%,#6b6e72)}
.about h2{position:absolute;left:638px;top:48px;font-size:32px;font-weight:700;color:var(--ink)}
.about h2 em{font-style:normal;color:var(--red)}
.about .rule{position:absolute;left:638px;top:100px;width:60px;height:3px;background:var(--red)}
.about p{position:absolute;left:638px;width:520px;font-size:15.5px;line-height:24px;text-align:justify}
/* why */
.feature{position:absolute;width:270px;text-align:center}
.feature h4{font-size:19px;font-weight:700;color:var(--ink);margin-bottom:12px}
.feature p{font-size:14px;line-height:20px}
.feature .go{width:24px;height:24px;border-radius:50%;margin:14px auto 0;display:flex;align-items:center;justify-content:center}
/* work */
.work{position:absolute;left:0;top:2405px;width:1200px;height:663px;background:var(--light)}
.work-card{position:absolute;top:156px;width:328px;height:403px;background:var(--white);box-shadow:0 0 0 1px #e2e2e2}
.work-card .logo-slot{height:75px;display:flex;align-items:center;justify-content:center;font-size:30px;font-weight:700}
.work-card .photo{height:136px;position:relative;background:linear-gradient(180deg,#c9ccd2,#8c8f96)}
.work-card .zoom{position:absolute;right:8px;bottom:8px;width:34px;height:34px;border-radius:50%;background:rgba(60,60,60,.8)}
.work-card .text{padding:14px 12px}
.work-card h5{font-size:17px;font-weight:700;color:var(--ink)}
.work-card .role{font-size:14.5px;color:var(--ink);margin:4px 0 10px}
.work-card p{font-size:14.5px;line-height:22px}
.dots{position:absolute;left:574px;top:600px;display:flex;gap:6px}
.dots span{width:12px;height:12px;border-radius:50%;background:var(--dark)}
.dots span:first-child{background:var(--red)}
/* clients */
.client{position:absolute;top:3211px;height:94px;display:flex;align-items:center;justify-content:center;font-size:24px;font-weight:700;text-align:center}
/* footer */
.site-footer{position:absolute;left:0;top:3370px;width:1200px;height:296px;background:var(--dark)}
.site-footer h6{position:absolute;top:46px;font-size:16px;font-weight:700;color:var(--white);text-transform:uppercase}
.site-footer h6 em{font-style:normal;color:var(--red)}
.vline{position:absolute;top:50px;width:1px;height:210px;background:#444}
.links{position:absolute;left:82px;top:92px;list-style:none;font-size:13px;color:#ddd;line-height:32px}
.links li::before{content:"• ";color:#ddd}
.links li.on{color:var(--red)}
.contact-row{position:absolute;left:285px;display:flex;gap:12px;font-size:14px;color:#ddd;line-height:20px}
.field{position:absolute;left:606px;width:268px;height:34px;border:1px solid #888;color:#ddd;font-size:13px;padding:8px 10px}
.foot-brand{position:absolute;left:990px;top:120px;font-size:44px;font-weight:700;color:var(--white)}
.copy{position:absolute;left:0;top:3666px;width:1200px;height:45px;background:var(--red);color:var(--white);font-size:13px;line-height:45px;padding:0 82px;display:flex;justify-content:space-between}
</style>
</head>
<body>

<header class="site-header">
  <div class="brand"><span class="brand-dot"></span><span class="brand-name">VARNO</span></div>
  <div class="brand-tag">Spark Every Day</div>
  <div class="topbar">
    <span class="ico"><svg width="14" height="14" viewBox="0 0 24 24"><path d="M6.6 10.8a15 15 0 0 0 6.6 6.6l2.2-2.2c.3-.3.7-.4 1-.2 1.1.4 2.3.6 3.6.6.6 0 1 .4 1 1V20c0 .6-.4 1-1 1A17 17 0 0 1 3 4c0-.6.4-1 1-1h3.5c.6 0 1 .4 1 1 0 1.3.2 2.5.6 3.6.1.3 0 .7-.2 1z" fill="#ec1f27"/></svg></span><span>131 722</span>
    <span class="ico"><svg width="14" height="14" viewBox="0 0 24 24"><rect x="2" y="5" width="20" height="14" fill="none" stroke="#ec1f27" stroke-width="2"/><path d="M2 5l10 8 10-8" fill="none" stroke="#ec1f27" stroke-width="2"/></svg></span><span>service@varnoelectrical-example.com.au</span>
    <div class="social"><span></span><span></span><span></span></div>
  </div>
  <nav class="main-nav">
    <a class="active">HOME</a><a>VARNO STORY</a><a>SERVICES</a><a>OUR WORK</a><a style="border:none">CONTACT US</a>
  </nav>
</header>

<section class="hero" role="img" aria-label="Electrician in hard hat and hi-vis vest working at a switchboard">
  <div class="hero-arrow" style="left:28px"><svg width="14" height="14" viewBox="0 0 10 10"><path d="M7 1L3 5l4 4" fill="none" stroke="#fff" stroke-width="2"/></svg></div>
  <div class="hero-arrow" style="right:28px"><svg width="14" height="14" viewBox="0 0 10 10"><path d="M3 1l4 4-4 4" fill="none" stroke="#fff" stroke-width="2"/></svg></div>
  <div class="hero-caption">Australia's largest fully integrated Electrical &amp; Energy Solutions Provider.</div>
</section>

<h2 class="sec-title" style="top:758px">Our <em>Services</em></h2>
<div class="service-card" style="left:82px"><h3>ELECTRICAL</h3><div class="photo" role="img" aria-label="Electrician wiring a switchboard" style="background:linear-gradient(135deg,#3d5d8a,#c8b04a 50%,#7d8794)"></div><span class="btn">Read more<i><svg width="8" height="8" viewBox="0 0 10 10"><path d="M3 1l4 4-4 4" fill="none" stroke="#fff" stroke-width="2"/></svg></i></span></div>
<div class="service-card" style="left:435px"><h3>LED LIGHTING</h3><div class="photo" role="img" aria-label="LED light bulbs" style="background:linear-gradient(135deg,#e6e6e6,#b8b8b8 60%,#d9d9d9)"></div><span class="btn">Read more<i><svg width="8" height="8" viewBox="0 0 10 10"><path d="M3 1l4 4-4 4" fill="none" stroke="#fff" stroke-width="2"/></svg></i></span></div>
<div class="service-card" style="left:794px"><h3>SOLAR POWER</h3><div class="photo" role="img" aria-label="Solar panels being installed on a roof" style="background:linear-gradient(160deg,#5b8fd0,#2c4f9a 55%,#1d2f63)"></div><span class="btn">Read more<i><svg width="8" height="8" viewBox="0 0 10 10"><path d="M3 1l4 4-4 4" fill="none" stroke="#fff" stroke-width="2"/></svg></i></span></div>

<section class="about">
  <div class="photo" role="img" aria-label="Large warehouse interior with overhead lighting"></div>
  <h2>ABOUT <em>VARNO</em></h2>
  <div class="rule"></div>
  <p style="top:128px">Varno Electrical was formed to be an expert Electricity Contracting Company providing services to all Residential and Commercial Customers. With over 10 years of experience, Varno Electrical has developed a highly-experienced team of professionals that ensure all our customer expectations are met.</p>
  <p style="top:262px">Lorem ipsum dolor sit amet, consectetuer adipiscing elit, sed diam nonummy nibh euismod tincidunt ut laoreet dolore magna aliquam erat volutpat. Ut wisi enim ad minim veniam.</p>
  <span class="btn abs" style="left:638px;top:356px">Read more<i><svg width="8" height="8" viewBox="0 0 10 10"><path d="M3 1l4 4-4 4" fill="none" stroke="#fff" stroke-width="2"/></svg></i></span>
</section>

<h2 class="sec-title" style="top:1694px">Why <em>Choose Us?</em></h2>

<div class="feature" style="left:75px;top:1796px"><h4>Professional Service</h4><p>When you hire a Varno Electrical Electrician you will get a professional and well-presented Electrician that comes skilled and ready to do the job.</p><div class="go" style="background:var(--red)"><svg width="8" height="8" viewBox="0 0 10 10"><path d="M3 1l4 4-4 4" fill="none" stroke="#fff" stroke-width="2"/></svg></div></div>
<div class="feature" style="left:459px;top:1796px"><h4>Value for Money</h4><p>We provide extremely competitive pricing, which means you get value for money on quality that is comparable to the best in the industry.</p><div class="go" style="background:var(--red)"><svg width="8" height="8" viewBox="0 0 10 10"><path d="M3 1l4 4-4 4" fill="none" stroke="#fff" stroke-width="2"/></svg></div></div>
<div class="feature" style="left:855px;top:1796px"><h4>Fully insured</h4><p>Varno Electrical is fully insured and equipped to handle break downs and service call outs.</p><div class="go" style="background:var(--red)"><svg width="8" height="8" viewBox="0 0 10 10"><path d="M3 1l4 4-4 4" fill="none" stroke="#fff" stroke-width="2"/></svg></div></div>

<svg class="abs" style="left:0;top:1960px" width="1200" height="240" viewBox="0 0 1200 240">
  <g fill="none" stroke-width="62">
    <path d="M82 110 H99 A99 99 0 0 0 297 110" stroke="#ec1f27"/>
    <path d="M297 110 A99 99 0 0 1 495 110" stroke="#2b2d36"/>
    <path d="M495 110 A99 99 0 0 0 693 110" stroke="#ec1f27"/>
    <path d="M693 110 A99 99 0 0 1 891 110" stroke="#2b2d36"/>
    <path d="M891 110 A99 99 0 0 0 1089 110 H1121" stroke="#ec1f27"/>
  </g>
  <g fill="#fff" stroke="#e3e3e3" stroke-width="6">
    <circle cx="198" cy="110" r="74"/><circle cx="396" cy="110" r="74"/><circle cx="594" cy="110" r="74"/><circle cx="792" cy="110" r="74"/><circle cx="990" cy="110" r="74"/>
  </g>
  <g fill="#2b2d36">
    <circle cx="192" cy="96" r="12"/><path d="M170 132c0-16 10-24 22-24s22 8 22 24z"/><circle cx="214" cy="124" r="9" fill="none" stroke="#2b2d36" stroke-width="5"/>
    <circle cx="396" cy="100" r="18" fill="none" stroke="#2b2d36" stroke-width="5"/><path d="M386 114l-8 26 9-4 5 8 4-22zM406 114l8 26-9-4-5 8-4-22z"/>
    <path d="M586 86h16l-4 8c14 6 20 18 20 30 0 10-10 14-24 14s-24-4-24-14c0-12 6-24 20-30z"/><text x="594" y="130" text-anchor="middle" font-size="22" font-weight="700" fill="#fff" font-family="Roboto,sans-serif">$</text>
    <circle cx="792" cy="110" r="24" fill="none" stroke="#2b2d36" stroke-width="5"/><path d="M772 110h40M792 86c-10 12-10 36 0 48M792 86c10 12 10 36 0 48" fill="none" stroke="#2b2d36" stroke-width="4"/>
    <path d="M990 82l24 8v18c0 16-10 26-24 32-14-6-24-16-24-32V90z"/><path d="M978 110l8 8 16-16" fill="none" stroke="#fff" stroke-width="5"/>
  </g>
</svg>

<div class="feature" style="left:246px;top:2188px;width:300px"><h4>5 year workmanship guarantee</h4><p>You can buy with confidence as all of our work has a 5 year workmanship guarantee. For your peace of mind, we unconditionally back our electrical work. We will come back to fix any problems at our own expense.</p><div class="go" style="background:var(--dark)"><svg width="8" height="8" viewBox="0 0 10 10"><path d="M3 1l4 4-4 4" fill="none" stroke="#fff" stroke-width="2"/></svg></div></div>
<div class="feature" style="left:642px;top:2188px;width:300px"><h4>Environmentally friendly</h4><p>We a committed to reducing carbon emissions by installing Solar Power and upgrading sites to LED Lighting. In addition to reducing the carbon emissions we recycle Fluorescent Tubes, Highbay Globes, Metal and Cardboard.</p><div class="go" style="background:var(--dark)"><svg width="8" height="8" viewBox="0 0 10 10"><path d="M3 1l4 4-4 4" fill="none" stroke="#fff" stroke-width="2"/></svg></div></div>

<section class="work">
  <h2 class="sec-title" style="top:52px">Our <em>Work</em></h2>
  <div class="work-card" style="left:82px">
    <div class="logo-slot" style="background:#f5e600;color:#222">Outback Gear Co</div>
    <div class="photo" role="img" aria-label="Retail store interior with new lighting"><span class="zoom"></span></div>
    <div class="text"><h5>Lena Morrow</h5><div class="role">Executive Outback Gear Co</div><p>The service, communication and after sales service of Varno Electrical has been awesome. We would strongly recommend them to any business contemplating upgrading.</p></div>
  </div>
  <div class="work-card" style="left:435px">
    <div class="logo-slot" style="color:#ec1f27">Nightlane</div>
    <div class="photo" role="img" aria-label="Shop interior with ceiling lights"><span class="zoom"></span></div>
    <div class="text"><h5>R. Castell</h5><div class="role">Balwyn North VIC</div><p>They clean up after the job, explained everything I needed to know and answered all questions, very professional. Will use them again in the future!</p></div>
  </div>
  <div class="work-card" style="left:794px">
    <div class="logo-slot" style="color:#1d6fb8">Stelvara</div>
    <div class="photo" role="img" aria-label="Industrial warehouse interior"><span class="zoom"></span></div>
    <div class="text"><h5>Dorvane</h5><div class="role">Cranbourne North VIC</div><p>Excellent work and very professional. Marcus takes time to explain everything and demonstrate workings. Very clear precise and accurate.</p></div>
  </div>
  <div class="dots"><span></span><span></span><span></span></div>
</section>

<h2 class="sec-title" style="top:3110px">Our Satisfied <em>Clients</em></h2>
<div class="client" style="left:129px;width:210px;color:#ec1f27;background:#fff">Nightlane</div>
<div class="client" style="left:371px;width:213px;background:#f5e600;color:#222">Outback Gear Co</div>
<div class="client" style="left:614px;width:215px;background:#ec1f27;color:#fff;font-size:20px">Heron Plumbing Supplies</div>
<div class="client" style="left:856px;width:213px;background:#d61f26;color:#fff;font-size:21px">Goldarch Burgers</div>

<footer class="site-footer">
  <h6 style="left:82px">Quick <em>Links</em></h6>
  <ul class="links"><li class="on">Home</li><li>Varno Story</li><li>Services</li><li>Our Work</li><li>Contact Us</li></ul>
  <div class="vline" style="left:240px"></div>
  <h6 style="left:285px">Contact <em>Details</em></h6>
  <div class="contact-row" style="top:92px"><svg width="14" height="18" viewBox="0 0 14 18"><path d="M7 0a7 7 0 0 0-7 7c0 5 7 11 7 11s7-6 7-11a7 7 0 0 0-7-7z" fill="#ec1f27"/><circle cx="7" cy="7" r="2.5" fill="#2b2d36"/></svg><div><b style="color:#fff">Varno</b><br>24/88 Halden Rd, Glen Hartley,<br>VIC 3150</div></div>
  <div class="contact-row" style="top:176px"><svg width="14" height="14" viewBox="0 0 24 24"><path d="M6.6 10.8a15 15 0 0 0 6.6 6.6l2.2-2.2c.3-.3.7-.4 1-.2 1.1.4 2.3.6 3.6.6.6 0 1 .4 1 1V20c0 .6-.4 1-1 1A17 17 0 0 1 3 4c0-.6.4-1 1-1h3.5c.6 0 1 .4 1 1 0 1.3.2 2.5.6 3.6.1.3 0 .7-.2 1z" fill="#ec1f27"/></svg>131 722</div>
  <div class="contact-row" style="top:224px"><svg width="14" height="14" viewBox="0 0 24 24"><rect x="2" y="5" width="20" height="14" fill="#ec1f27"/><path d="M2 5l10 8 10-8" fill="none" stroke="#2b2d36" stroke-width="2"/></svg>service@varnoelectrical-example.com.au</div>
  <div class="vline" style="left:570px"></div>
  <h6 style="left:606px">Quick <em>Inquiry</em></h6>
  <div class="field" style="top:92px">Name</div>
  <div class="field" style="top:134px">Email</div>
  <div class="field" style="top:176px;height:44px">Message</div>
  <span class="btn abs" style="left:606px;top:232px;height:26px;font-size:12px;padding-left:16px">Submit<i style="width:18px;height:18px"><svg width="7" height="7" viewBox="0 0 10 10"><path d="M3 1l4 4-4 4" fill="none" stroke="#fff" stroke-width="2"/></svg></i></span>
  <div class="vline" style="left:920px"></div>
  <div class="foot-brand">VARNO</div>
  <div class="abs" style="left:990px;top:180px;font-size:14px;color:#ddd">Spark Every Day</div>
  <div class="social abs" style="left:990px;top:214px"><span></span><span></span><span></span></div>
</footer>
<div class="copy"><span>Copyright © 2017 Varno. All Right Reserved.</span><span>Terms and Conditions &nbsp;|&nbsp; Privacy</span></div>

</body>
</html>
```